AUTOMOTIVE/ CAR REPAIRS / CRASH REPAIRS / PAINT SPRAYING AND PANEL BEATING

AUTOMOTIVE REPAIR. CAR / MOTORCYCLES GOT LOGO DESIGN / DID THINK ABOUT FOLIA DONT NOALREADY HAVE WEB ADRESS www.brenvashine.co.uk and mail sales@brenvashine,co.uk NEED SOMETHINK I CAN MANAGE TO UPLOAD PICTURES IN TO A GALLERY OR SOMETHINGLIKE THAT I ALSO SELL CAR AND MOTORCYCLES MAYBE A SELLS PAGE WITH A TILLWAVE LINK

Target Market(s)

TRADE / GENERAL PUBLIC

Industry/Entity Type

Automotive

Coding

Coded - Design and coding required

Number of Pages Required

4 page

Font styles to use
Serif
Sans Serif

Colors

Designer to choose colors to be used in the design.

Requirements
Must have
• GALLERY/ SHOP TO SALE CARS AND MOTORCYCLE / LOGOS OF MATERIALS I USE DORFLINT / KEBO / VASTINCO / Q WRAP / GLENBRUSH
• CONTACT US
Nice to have
• TILLWAVE / EASY TO MANAGE / VIDEO CLIP OF DORFLINT HUE PLANNER Z7
• SWIFT BLEND PAINT TONVIEW WETLINE AND TULVOKE

```html
<!DOCTYPE html>
<html lang="en">
<head>
<meta charset="utf-8">
<title>Brenvashine Bodyshop</title>
<link href="https://fonts.googleapis.com/css2?family=Mulish:wght@400;600;700;800&family=Open+Sans:wght@400;600;700&display=swap" rel="stylesheet">
<style>
:root{
  --ink:#14171e;
  --dark:#1b1e25;
  --red:#a80f14;
  --text:#2b2b2b;
  --muted:#666;
  --grey:#e4e4e4;
  --card:#f2f2f2;
  --white:#fff;
  --navy:#1f2633;
}
*{box-sizing:border-box;margin:0;padding:0}
html,body{width:1200px;height:4633px;overflow:hidden}
body{font-family:'Mulish',sans-serif;color:var(--text);background:var(--white);position:relative}
.abs{position:absolute}
.center{left:0;width:1200px;text-align:center}
.btn-pill{display:inline-block;border-radius:20px;background:linear-gradient(#fff,#cfcfcf);color:#222;font-size:13px;font-weight:700;padding:10px 22px;letter-spacing:.5px;box-shadow:0 2px 4px rgba(0,0,0,.4)}
.btn-dark{display:inline-block;border-radius:20px;background:var(--navy);color:#fff;font-size:14px;font-weight:700;padding:11px 26px}
.btn-ghost{display:inline-block;border:1px solid #aaa;border-radius:16px;font-size:10px;color:#555;padding:7px 14px;font-family:'Open Sans',sans-serif}
h2.red{color:var(--red);font-size:34px;font-weight:800}

/* header */
.site-header{top:0;left:0;width:1200px;height:63px;background:var(--dark);z-index:3}
.brand{left:144px;top:14px;color:#fff;font-size:20px;font-weight:800;letter-spacing:3px;text-align:center;line-height:1}
.brand small{display:block;font-size:9px;letter-spacing:5px;font-weight:600;margin-top:4px}
.nav{right:144px;top:24px;display:flex;gap:32px;font-size:12px;color:#fff}
.nav .active{color:#e2302f}

/* hero */
.hero{top:0;left:0;width:1200px;height:690px}
.hero-title{top:260px;color:#fff;font-size:48px;font-weight:800}
.hero-sub{top:318px;color:#fff;font-size:31px;font-weight:400}
.hero-btn{top:372px}
.arrow{top:325px;width:26px;height:26px}

/* about */
.about h2{top:780px}
.about .lead{top:826px;font-size:16px}
.about .strong{top:860px;left:150px;width:900px;font-size:14px;font-weight:700;font-family:'Open Sans',sans-serif;line-height:24px}
.about .body{top:915px;left:148px;width:904px;font-size:11px;font-family:'Open Sans',sans-serif;line-height:22.5px;text-align:center}

/* what we do */
.whatwedo{top:1080px;left:0;width:1200px;height:401px}
.whatwedo h2{top:1220px;color:#fff;font-size:32px;font-weight:700}
.whatwedo p{top:1265px;color:#fff;font-size:15px}
.whatwedo .cta{top:1297px}

/* why us */
.why h2{top:1552px}
.why .intro{top:1596px;left:148px;width:904px;font-size:15.5px;line-height:26px;text-align:center}
.why .note{top:1703px;font-size:11px;font-family:'Open Sans',sans-serif;color:#555}
.card{background:var(--card);padding:22px 20px 0;font-family:'Open Sans',sans-serif}
.card h3{font-size:14px;font-weight:700;margin:14px 0 10px;font-family:'Mulish',sans-serif}
.card p{font-size:10.5px;line-height:18px;color:#333;min-height:56px}
.card .btn-ghost{position:absolute;bottom:14px;left:20px}
.icon{width:70px;height:70px}

/* gallery */
.gallery{top:2304px;left:0;width:1200px;height:640px}
.gallery h2{top:2372px;color:#fff;font-size:32px;font-weight:700}
.photo{border-radius:0}
.viewall{top:2793px}

/* materials */
.materials-label{top:3024px;font-size:14px;font-weight:700}
.partner{top:3070px;height:60px;display:flex;align-items:center;gap:8px;font-size:20px;font-weight:800;color:var(--ink)}
.partner i{display:block;width:18px;height:18px;background:var(--red);border-radius:50%}

/* customisation */
.custom h2{top:3254px}
.custom p{top:3303px;left:150px;width:900px;font-size:15.5px;line-height:23px;text-align:center}
.custom .tag{top:3360px;font-size:13.5px;font-weight:700}
.custom .cta{top:3388px}

/* appointment */
.appt{top:3470px;left:0;width:1200px;height:400px;background:var(--grey)}
.appt h2{top:3518px}
.appt .addr{top:3570px;font-size:15.5px}
.field{background:#fff;border:1px solid #ddd;height:42px;display:flex;align-items:center;justify-content:space-between;padding:0 16px;color:#999;font-size:15px}
.appt .cta{top:3744px}
.appt .note{top:3800px;font-size:11px;font-family:'Open Sans',sans-serif;color:#666}

/* contact */
.contact h2{top:3944px}
.contact-box{top:4000px;left:144px;width:456px;height:198px;background:#e6e6e6}
.contact-row{left:230px;display:flex;font-size:12px;font-family:'Open Sans',sans-serif;color:#333;line-height:18px}
.contact-row svg{position:absolute;left:-34px;top:2px}
.map{top:4000px;left:600px;width:456px;height:198px}

/* footer */
.footer-col h4{color:#fff;font-size:16px;font-weight:700;margin-bottom:10px}
.footer-col li{list-style:none;color:#8a8f99;font-size:10.5px;line-height:22px;font-family:'Open Sans',sans-serif}
.pay{display:inline-block;background:#5f6572;color:#dde;font-size:7px;font-weight:700;padding:5px 4px;margin-right:4px;border-radius:2px;letter-spacing:.3px}
.social{right:144px;top:4586px;display:flex;gap:18px;align-items:center;color:#8a8f99;font-size:11px}
.social span{display:flex;align-items:center;gap:5px}
.social i{display:block;width:8px;height:8px;border-radius:50%;background:#8a8f99}
</style>
</head>
<body>

<!-- hero -->
<div class="abs hero" role="img" aria-label="Red sports car driving on a mountain road at dusk under a dark cloudy sky">
  <svg width="1200" height="690" class="abs" style="top:0;left:0">
    <defs>
      <linearGradient id="heroSky" x1="0" y1="0" x2="0" y2="1">
        <stop offset="0" stop-color="#3d4248"/>
        <stop offset=".45" stop-color="#23262c"/>
        <stop offset="1" stop-color="#0e1013"/>
      </linearGradient>
      <radialGradient id="heroCar" cx=".55" cy=".55" r=".3">
        <stop offset="0" stop-color="#7a1418" stop-opacity=".8"/>
        <stop offset="1" stop-color="#7a1418" stop-opacity="0"/>
      </radialGradient>
    </defs>
    <polygon points="0,0 1200,0 1200,612 600,690 0,612" fill="url(#heroSky)"/>
    <polygon points="0,0 1200,0 1200,612 600,690 0,612" fill="url(#heroCar)"/>
  </svg>
</div>

<header class="abs site-header">
  <div class="abs brand">BRENVASHINE<small>BODYSHOP</small></div>
  <nav class="abs nav"><span class="active">HOME</span><span>ABOUT US</span><span>SERVICES</span><span>CUSTOM</span><span>GALLERY</span><span>CONTACT</span></nav>
</header>

<div class="abs center hero-title">YOUR ONE STOP BODY SHOP</div>
<div class="abs center hero-sub">The home of paint perfection</div>
<div class="abs center hero-btn"><span class="btn-pill">SHOP NOW</span></div>
<svg class="abs arrow" style="left:50px" viewBox="0 0 26 26"><path d="M17 3 7 13l10 10" stroke="#fff" stroke-width="4" fill="none"/></svg>
<svg class="abs arrow" style="left:1122px" viewBox="0 0 26 26"><path d="M9 3l10 10L9 23" stroke="#fff" stroke-width="4" fill="none"/></svg>

<!-- about -->
<section class="about">
  <h2 class="abs center red">BRENVASHINE YOUR ONE STOP BODYSHOP</h2>
  <p class="abs center lead">Fully qualified trained technicians family run business established over 30 years</p>
  <p class="abs strong" style="text-align:center">Brenvashine, based in Thornvale, Ashmoor established in August, 1985 has grown to become Ashmoor's premiere manufacturer approved accident repair centre.</p>
  <p class="abs body">Equipped with the latest technology and factory trained technicians, we process accident repairs for all leading insurance and vehicle management companies, specialising in accident repairs for most prestige vehicles manufacturers. We are proud to maintain a close working partnership with several local dealership networks. Brenvashine aims to continually set new standards of quality control and customer care, by ensuring an accident repair service which exceeds all expectations whilst providing a fully guaranteed, quality repair to meet the customers needs.</p>
</section>

<!-- what we do -->
<div class="abs whatwedo" role="img" aria-label="Dark close-up of a luxury car front grille in a workshop" style="background:linear-gradient(120deg,#2a2d33 0%,#1a1c21 50%,#0f1013 100%)"></div>
<h2 class="abs center whatwedo" style="top:1220px;height:auto;color:#fff;font-size:32px;font-weight:700">WHAT WE DO</h2>
<p class="abs center" style="top:1265px;color:#fff;font-size:15px">From the repair of the smallest dents and scratches to major auto repair work, Brenvashine is set up to meet your needs.</p>
<div class="abs center" style="top:1297px"><span class="btn-pill">CONTACT US</span></div>

<!-- why us -->
<section class="why">
  <h2 class="abs center red">WHY US</h2>
  <p class="abs intro">As a small company we are able to offer an exceptionally personal service. Whenever you call us we aim for you to be able to speak directly to the person performing your car body repairs, who will give you plain speaking, objective advice. This, combined with our many years' experience and competitive prices makes us the perfect choice for those in need of any car body repair.</p>
  <p class="abs center note">(Please call or email us from our contact page to arrange a estimate appointment)</p>

  <div class="abs card" style="top:1744px;left:144px;width:297px;height:223px">
    <svg class="icon" viewBox="0 0 70 70" fill="none" stroke="#b5121b" stroke-width="2.5"><rect x="6" y="32" width="40" height="18" rx="3"/><path d="M12 32l6-10h18l6 10"/><circle cx="16" cy="52" r="5"/><circle cx="38" cy="52" r="5"/><path d="M50 14h12v10H50zM56 24v14"/></svg>
    <h3>Full or part resprays</h3>
    <p>Single panel resprays to full car resprays</p>
    <span class="btn-ghost">READ MORE</span>
  </div>
  <div class="abs card" style="top:1744px;left:451px;width:298px;height:223px">
    <svg class="icon" viewBox="0 0 70 70" fill="none" stroke="#b5121b" stroke-width="2.5"><path d="M35 6l10 18H25z"/><path d="M35 13v6"/><rect x="12" y="38" width="46" height="14" rx="3"/><path d="M18 38l6-8h22l6 8"/><circle cx="20" cy="54" r="5"/><circle cx="50" cy="54" r="5"/></svg>
    <h3>Dent &amp; scratch removal</h3>
    <p>From small paintless dent repairs to full panel replacements. Scratches, chips &amp; paint repairs undertaken</p>
    <span class="btn-ghost">READ MORE</span>
  </div>
  <div class="abs card" style="top:1744px;left:758px;width:298px;height:223px">
    <svg class="icon" viewBox="0 0 70 70" fill="none" stroke="#b5121b" stroke-width="2.5"><path d="M6 34h58v10c0 6-4 10-10 10H16C10 54 6 50 6 44z"/><path d="M16 34l6-10h26l6 10"/><path d="M18 44h34"/></svg>
    <h3>Bumper repair</h3>
    <p>Bumper scuffs, plastic bumper repairs and full bumper replacements. Full factory matched colours.</p>
    <span class="btn-ghost">READ MORE</span>
  </div>
  <div class="abs card" style="top:1978px;left:144px;width:452px;height:248px">
    <svg class="icon" viewBox="0 0 70 70" fill="none" stroke="#b5121b" stroke-width="2.5"><rect x="8" y="34" width="44" height="16" rx="3"/><path d="M14 34l6-10h20l6 10"/><circle cx="18" cy="52" r="5"/><circle cx="42" cy="52" r="5"/><path d="M54 10l4 8 8-2-6 6 4 8-8-4-6 6 1-8"/></svg>
    <h3>Accident repair</h3>
    <p>All accident repair undertaken, Just one call to Brenvashine and we'll help you take the first steps towards getting your vehicle repaired and back on the road.</p>
    <span class="btn-ghost">READ MORE</span>
  </div>
  <div class="abs card" style="top:1978px;left:605px;width:451px;height:248px">
    <svg class="icon" viewBox="0 0 70 70" fill="none" stroke="#b5121b" stroke-width="2.5"><circle cx="35" cy="35" r="30"/><circle cx="35" cy="35" r="22"/><circle cx="35" cy="35" r="6"/><path d="M35 13v16M35 41v16M13 35h16M41 35h16M20 20l11 11M39 39l11 11M50 20 39 31M31 39 20 50"/></svg>
    <h3>Alloy wheel's refurbished, repaired &amp; painted</h3>
    <p>Etiam vel massa elementum, bibendum tellus venenatis, feugiat massa. Curabitur venenatis lacinia ornare. Cras sollicitudin cursus dui eu placerat.</p>
    <span class="btn-ghost">READ MORE</span>
  </div>
</section>

<!-- gallery -->
<svg class="abs" style="top:2304px;left:0" width="1200" height="670">
  <rect x="0" y="0" width="1200" height="583" fill="var(--ink)"/>
  <rect x="0" y="583" width="1200" height="87" fill="var(--grey)"/>
  <polygon points="0,583 1200,583 600,662" fill="var(--ink)"/>
</svg>
<h2 class="abs center" style="top:2372px;color:#fff;font-size:32px;font-weight:700">GALLERY</h2>
<div class="abs photo" role="img" aria-label="Black sports car in a workshop" style="top:2432px;left:144px;width:218px;height:158px;background:linear-gradient(135deg,#4a5563,#1c1f26)"></div>
<div class="abs photo" role="img" aria-label="Motorcycle parked on a road at sunset" style="top:2608px;left:144px;width:218px;height:160px;background:linear-gradient(135deg,#8a6a4a,#2b2620)"></div>
<div class="abs photo" role="img" aria-label="Black estate car parked outside the bodyshop unit" style="top:2432px;left:373px;width:454px;height:336px;background:linear-gradient(180deg,#9aa4ae 0%,#7d858c 40%,#2a2d31 75%,#6b6d6e 100%)"></div>
<div class="abs photo" role="img" aria-label="Red supercar in a workshop" style="top:2432px;left:838px;width:218px;height:158px;background:linear-gradient(135deg,#6e737a,#b23a22)"></div>
<div class="abs photo" role="img" aria-label="Red car stripped for repair in the spray booth" style="top:2608px;left:838px;width:218px;height:160px;background:linear-gradient(135deg,#c9ccd0,#9a1c1c)"></div>
<div class="abs center viewall"><span class="btn-pill">VIEW ALL</span></div>

<!-- materials -->
<div class="abs" style="top:2974px;left:0;width:1200px;height:208px;background:var(--grey)"></div>
<p class="abs center materials-label">Materials i use...</p>
<div class="abs partner" style="left:144px"><i></i>DORFLINT</div>
<div class="abs partner" style="left:380px">KEBO</div>
<div class="abs partner" style="left:543px"><i style="border-radius:0"></i>VASTINCO</div>
<div class="abs partner" style="left:748px">Q WRAP</div>
<div class="abs partner" style="left:940px"><i></i>GLENBRUSH</div>

<!-- customisation -->
<section class="custom">
  <h2 class="abs center red">CUSTOMISATION</h2>
  <p class="abs">Our experienced team can efficiently carry out any customising work you require in order to meet the specific design you have in mind.</p>
  <p class="abs center tag">BRENVASHINE CAN ENHANCE YOUR CAR</p>
  <div class="abs center cta"><span class="btn-dark">READ MORE</span></div>
</section>

<!-- appointment -->
<div class="abs appt"></div>
<h2 class="abs center red" style="top:3518px">ARRANGE A FREE ESTIMATE APPOINTMENT</h2>
<p class="abs center" style="top:3570px;font-size:15.5px">Brenvashine Bodyshop, Kestrel business park, Ferry lane, Thornvale, Ashmoor, AS12 7QP</p>
<div class="abs field" style="top:3616px;left:168px;width:420px">Date
  <svg width="14" height="14" viewBox="0 0 14 14"><rect x="1" y="3" width="12" height="10" fill="none" stroke="#999"/><path d="M1 6h12M4 1v3M10 1v3" stroke="#999"/></svg></div>
<div class="abs field" style="top:3616px;left:608px;width:424px">Time
  <svg width="14" height="14" viewBox="0 0 14 14"><circle cx="7" cy="7" r="6" fill="none" stroke="#999"/><path d="M7 3v4h3" stroke="#999" fill="none"/></svg></div>
<div class="abs field" style="top:3681px;left:168px;width:864px">Price
  <svg width="14" height="10" viewBox="0 0 14 10"><path d="M1 2l6 6 6-6" stroke="#666" stroke-width="2" fill="none"/></svg></div>
<div class="abs center" style="top:3744px"><span class="btn-dark">BOOK APPOINTMENT</span></div>
<p class="abs center" style="top:3800px;font-size:11px;font-family:'Open Sans',sans-serif;color:#666">If you are unable to keep your appointment, please contact us as soon as possible.</p>

<!-- contact -->
<section class="contact">
  <h2 class="abs center red">CONTACT INFO</h2>
  <div class="abs contact-box"></div>
  <div class="abs contact-row" style="top:4036px">
    <svg width="12" height="14" viewBox="0 0 12 14"><path d="M6 13S1 7.5 1 5a5 5 0 0 1 10 0c0 2.5-5 8-5 8z" fill="#444"/><circle cx="6" cy="5" r="1.8" fill="#e6e6e6"/></svg>
    <span>Kestrel Business park,<br>Ferry Lane, Thornvale, Ashmoor, AS12 7QP</span></div>
  <div class="abs contact-row" style="top:4090px">
    <svg width="13" height="13" viewBox="0 0 13 13"><path d="M3 1l2 3-1.5 1.5a8 8 0 0 0 4 4L9 8l3 2-1 2.5C6 12.5.5 7 .5 2z" fill="#444"/></svg>
    <span>0770 900 4127</span></div>
  <div class="abs contact-row" style="top:4131px">
    <svg width="14" height="11" viewBox="0 0 14 11"><rect width="14" height="11" fill="#444"/><path d="M0 0l7 6 7-6" stroke="#e6e6e6" fill="none"/></svg>
    <span>sales@brenvashine.co.uk</span></div>
  <div class="abs map" role="img" aria-label="Street map showing the bodyshop location" style="background:linear-gradient(90deg,#ebebeb 0%,#ebebeb 72%,#b5dcbf 78%,#b5dcbf 100%)"></div>
</section>

<!-- footer -->
<svg class="abs" style="top:4280px;left:0" width="1200" height="353">
  <polygon points="0,76 600,0 1200,76 1200,353 0,353" fill="var(--ink)"/>
  <line x1="144" y1="279" x2="1056" y2="279" stroke="#3a3f4a"/>
</svg>
<div class="abs footer-col" style="top:4385px;left:144px"><h4>CUSTOMER SERVICES</h4><ul><li>Full or part resprays</li><li>Dents &amp; scratch removal</li><li>Bumper repair</li><li>Accident repair</li><li>Alloy wheel's refurbished, repaired &amp; painted</li></ul></div>
<div class="abs footer-col" style="top:4385px;left:440px"><h4>Links</h4><ul><li>About us</li><li>Customisation</li><li>Gallery</li><li>Contact</li></ul></div>
<div class="abs footer-col" style="top:4385px;left:586px"><h4>Payments</h4>
  <div><span class="pay">TILLWAVE</span><span class="pay">VANTA</span><span class="pay">STRIVO</span><span class="pay">MERIX</span><span class="pay">AMBRO</span></div></div>
<svg class="abs" style="top:4378px;left:848px" width="106" height="80"><circle cx="53" cy="40" r="36" fill="#c9a13a"/><circle cx="53" cy="40" r="27" fill="#1e1e1e"/></svg>
<p class="abs" style="top:4488px;left:850px;font-size:10px;line-height:18px;color:#8a8f99;font-family:'Open Sans',sans-serif">We stand apart from the rest<br>we strive to provide an exceptional service</p>
<p class="abs" style="top:4590px;left:144px;font-size:10px;color:#8a8f99;font-family:'Open Sans',sans-serif">Copyright © 2019 Brenvashine. All rights reserved.</p>
<div class="abs social"><span><i></i>Folia</span><span><i></i>Chirpa</span><span><i></i>Vidora</span><span><i></i>Snapla</span>
  <svg width="18" height="13" viewBox="0 0 18 13"><rect width="18" height="13" fill="#8a8f99"/><path d="M0 0l9 7 9-7" stroke="#14171e" fill="none" stroke-width="1.5"/></svg></div>

</body>
</html>
```